Business Card Design for company

We want new business cards. We'd like something different-- yet still highly professional. Our tagline is Shaping strategy, engineering results. Stock photos are ok, as long as they are relevant and look upscale.

Target Market(s)

Architecture/Business Management Consulting/Engineering Consulting

Contact Information for Business Card

dark gray background with pops of blue might be good, but you tell me. You're the designers. Rounded corners might be nice, but again, you tell me.

Font styles to use
Serif
Sans Serif

Colors
3276b5
5c5c5c
9d9d9d
fbfbfb

Requirements
Nice to have
• Something different, but still very professional.

```html
<!DOCTYPE html>
<html lang="en">
<head>
<meta charset="utf-8">
<title>Varden Partners – Business Card</title>
<link rel="stylesheet" href="https://fonts.googleapis.com/css2?family=Montserrat:wght@500;600&family=Lato:wght@400&display=swap">
<style>
  :root {
    --canvas: #9a9a9a;
    --card-light: #ffffff;
    --card-dark: #4a4d52;
    --brand-blue: #2e6aa3;
    --ink-gray: #4b4e53;
    --text-dark: #333333;
    --rule: #d6d6d6;
    --white: #fbfbfb;
  }
  * { margin: 0; padding: 0; box-sizing: border-box; }
  html, body { width: 1200px; height: 900px; overflow: hidden; }
  body { background: var(--canvas); position: relative; font-family: "Lato", sans-serif; }

  .card { position: absolute; height: 295px; width: 478px; }
  .card-front {
    left: 120px; top: 275px; background: var(--card-light);
    border-radius: 0 48px 0 48px;
  }
  .card-back {
    left: 607px; top: 274px; background: var(--card-dark);
    border-radius: 48px 0 48px 0; height: 293px; width: 477px;
  }

  .wordmark {
    position: absolute; font-family: "Montserrat", sans-serif; font-weight: 600;
    line-height: 1; text-align: right;
  }
  .card-front .wordmark { right: 33px; top: 46px; color: var(--brand-blue); }
  .wordmark .wordmark-main { display: block; font-size: 58px; letter-spacing: 1px; }
  .wordmark .wordmark-sub { display: block; font-size: 21px; letter-spacing: 2px; margin-top: 10px; }
  .card-back .wordmark { left: 0; right: 0; top: 92px; text-align: center; color: var(--brand-blue); }

  .holder { position: absolute; left: 30px; top: 162px; }
  .holder-name { font-family: "Montserrat", sans-serif; font-weight: 600; font-size: 17px; color: var(--ink-gray); }
  .holder-name .first { color: var(--brand-blue); }
  .holder-role { font-size: 13px; color: var(--text-dark); margin-top: 1px; }
  .divider { position: absolute; left: 148px; top: 189px; width: 297px; height: 1px; background: var(--rule); }

  .contacts { position: absolute; left: 30px; top: 203px; list-style: none; font-size: 13px; color: var(--text-dark); }
  .contacts li { display: flex; align-items: center; height: 17.5px; }
  .contacts svg { width: 11px; height: 11px; margin-right: 3px; fill: var(--brand-blue); }

  .address { position: absolute; right: 33px; top: 236px; font-size: 13px; color: var(--text-dark); text-align: right; line-height: 17px; }

  .tagline {
    position: absolute; left: 0; right: 0; top: 240px; text-align: center;
    font-family: "Montserrat", sans-serif; font-weight: 600; font-size: 15.5px; color: var(--white);
  }
</style>
</head>
<body>
  <section class="card card-front">
    <div class="wordmark">
      <span class="wordmark-main">VARDEN</span>
      <span class="wordmark-sub">PARTNERS</span>
    </div>
    <div class="holder">
      <p class="holder-name"><span class="first">DEREK</span> HOLLOWAY</p>
      <p class="holder-role">Managing Director</p>
    </div>
    <div class="divider"></div>
    <ul class="contacts">
      <li><svg viewBox="0 0 12 12"><path d="M1 4c0-2 2-3 5-3s5 1 5 3l-2 1-1-2H4L3 5zM2 6h8l1 5H1z"/></svg>044-555 210 384</li>
      <li><svg viewBox="0 0 12 12"><path d="M3 0h6v12H3zM4 1.5v8h4v-8z"/></svg>044-555 871 062</li>
      <li><svg viewBox="0 0 12 12"><path d="M0 2h12v8H0zM1 3l5 4 5-4z" fill-rule="evenodd"/></svg>info@varden.co</li>
      <li><svg viewBox="0 0 12 12"><circle cx="6" cy="6" r="5.5"/></svg>www.vardenpartners.co</li>
    </ul>
    <p class="address">48 Harbour Street, Suite 9<br>Northbridge, 204518</p>
  </section>

  <section class="card card-back">
    <div class="wordmark">
      <span class="wordmark-main">VARDEN</span>
      <span class="wordmark-sub">PARTNERS</span>
    </div>
    <p class="tagline">SHAPING STRATEGY, ENGINEERING RESULTS</p>
  </section>
</body>
</html>
```